BOLD & MINIMALIST DESIGN NEEDED

We want a very bold but minimalistic business card design that is impactful and utilizes both sides of the business card. Our current logo is included for your use.

We want bold fonts and good use of negative space. We don't want the logo to overpower the design.

Target Market(s)

Professionals who are building new commercial buildings.

Industry/Entity Type

Construction

Contact Information for Business Card

Name, Title, email, office phone, cell phone, website

Font styles to use
Serif
Sans Serif

Requirements
Must have
• Bold design!

```html
<!DOCTYPE html>
<html lang="en">
<head>
<meta charset="utf-8">
<title>Ridgeline Design + Build — Business Card</title>
<link href="https://fonts.googleapis.com/css2?family=Arimo:wght@400;700&display=swap" rel="stylesheet">
<style>
  :root {
    --stage: #2e2e2f;
    --card: #f7f7f7;
    --card-shade: #e9e9e9;
    --ink: #111111;
    --muted: #444444;
    --accent: #6cc04a;
    --curve: #dcdcdc;
  }
  * { margin: 0; padding: 0; box-sizing: border-box; }
  html, body { width: 1200px; height: 900px; overflow: hidden; }
  body {
    background: var(--stage);
    font-family: "Arimo", Arial, sans-serif;
    color: var(--ink);
    display: flex;
    flex-direction: column;
    align-items: center;
    justify-content: center;
    gap: 44px;
  }
  .card {
    position: relative;
    width: 660px;
    height: 377px;
    border-radius: 30px;
    background: linear-gradient(135deg, var(--card-shade) 0%, var(--card) 55%, #ffffff 100%);
    overflow: hidden;
  }

  /* Front */
  .card--front { display: flex; align-items: center; justify-content: center; }
  .brand { display: flex; align-items: center; gap: 14px; }
  .brand__mark { width: 22px; height: 22px; background: var(--accent); }
  .brand__name {
    font-weight: 700;
    color: var(--ink);
    text-transform: uppercase;
    letter-spacing: 1px;
  }
  .card--front .brand__name { font-size: 34px; }

  /* Back */
  .card--back .curve { position: absolute; left: 0; bottom: 0; width: 100%; height: 140px; }
  .person { position: absolute; left: 44px; top: 118px; }
  .person__name { font-size: 20px; font-weight: 400; }
  .person__title { font-size: 15px; color: var(--muted); }
  .person__divider { margin: 0 6px; font-size: 20px; }
  .person__cell {
    margin-top: 10px; display: flex; align-items: center; gap: 10px;
    font-size: 15px; color: #9a9a9a;
  }
  .contact {
    position: absolute; right: 46px; top: 100px; width: 260px;
    list-style: none; font-size: 13.5px; color: var(--muted);
  }
  .contact li { display: flex; align-items: flex-start; gap: 9px; line-height: 1.5; }
  .contact svg { flex: none; margin-top: 3px; }
  .contact__rule { position: absolute; right: 46px; top: 222px; width: 260px; height: 2px; background: var(--accent); }
  .card--back .brand { position: absolute; right: 46px; top: 250px; }
  .card--back .brand__name { font-size: 22px; }
  .card--back .brand__mark { width: 16px; height: 16px; }
</style>
</head>
<body>

  <section class="card card--front" aria-label="Card front">
    <div class="brand">
      <span class="brand__mark"></span>
      <span class="brand__name">Ridgeline Design + Build</span>
    </div>
  </section>

  <section class="card card--back" aria-label="Card back">
    <svg class="curve" viewBox="0 0 660 140" preserveAspectRatio="none" aria-hidden="true">
      <path d="M0 140 Q 320 20 660 60 L660 140 Z" fill="var(--curve)" opacity="0.45"/>
      <path d="M0 140 Q 320 36 660 74 L660 140 Z" fill="#ffffff" opacity="0.7"/>
    </svg>

    <div class="person">
      <p><span class="person__name">Jordan Ellis</span><span class="person__divider">|</span><span class="person__title">Founder</span></p>
      <p class="person__cell">
        <svg width="11" height="16" viewBox="0 0 11 16" aria-hidden="true"><rect x="1" y="1" width="9" height="14" rx="1.5" fill="none" stroke="var(--accent)" stroke-width="1.6"/></svg>
        3XX-2XX-9XXX
      </p>
    </div>

    <ul class="contact">
      <li>
        <svg width="12" height="12" viewBox="0 0 24 24" aria-hidden="true"><path fill="var(--ink)" d="M6.6 10.8a15 15 0 0 0 6.6 6.6l2.2-2.2a1 1 0 0 1 1-.25 11.4 11.4 0 0 0 3.6.57 1 1 0 0 1 1 1V20a1 1 0 0 1-1 1A17 17 0 0 1 3 4a1 1 0 0 1 1-1h3.5a1 1 0 0 1 1 1c0 1.25.2 2.45.57 3.57a1 1 0 0 1-.25 1z"/></svg>
        555-014-2200
      </li>
      <li>
        <svg width="13" height="10" viewBox="0 0 26 20" aria-hidden="true"><rect x="1" y="1" width="24" height="18" fill="var(--ink)"/><path d="M1 1 L13 11 L25 1" fill="none" stroke="#fff" stroke-width="2"/></svg>
        info@rdb-build.com
      </li>
      <li>
        <svg width="12" height="12" viewBox="0 0 24 24" aria-hidden="true"><g fill="none" stroke="var(--ink)" stroke-width="2"><circle cx="12" cy="12" r="10"/><ellipse cx="12" cy="12" rx="4.5" ry="10"/><path d="M2 12h20M4 7h16M4 17h16"/></g></svg>
        www.rdb-build.com
      </li>
      <li>
        <svg width="11" height="14" viewBox="0 0 20 26" aria-hidden="true"><path fill="var(--ink)" d="M10 0a10 10 0 0 0-10 10c0 7 10 16 10 16s10-9 10-16A10 10 0 0 0 10 0zm0 14a4 4 0 1 1 0-8 4 4 0 0 1 0 8z"/></svg>
        <span>418 Cedar Hollow Rd.<br>Pine Ridge, GA 30000</span>
      </li>
    </ul>
    <span class="contact__rule"></span>

    <div class="brand">
      <span class="brand__mark"></span>
      <span class="brand__name">Ridgeline Design + Build</span>
    </div>
  </section>

</body>
</html>
```